Plakat-Design für Immobilienmakler und Baufinanzierer
Zielgruppe
Wir sind Immobilienmakler und Baufinanzierer und suchen ein hochwertiges Design, unsere Zielgruppe sind Kunden, die Ihr Haus verkaufen möchten. Für jeden erfolgreichen Verkauf spenden wir 5 % unserer Maklercourtage an einen Verein, den sich der Kunde aussuchen darf. Mit diesem Plakat wollen wir auf unsere Vereinsförderng aufmerksam machen und Vereine ansprechen.
Aufgabenstellung
Text: 'Wir spenden 5 % unserer Provision für Ihren Verein', 'Nur 1,99 % Maklercourtage', Logo, Kontaktdaten

```html
<!DOCTYPE html>
<html lang="de">
<head>
<meta charset="utf-8">
<title>Haldwick Immobilien – Vereinsförderung</title>
<link href="https://fonts.googleapis.com/css2?family=Raleway:wght@400;500;700&display=swap" rel="stylesheet">
<style>
  :root {
    --teal: #0b6f80;
    --wine: #8e1a2d;
    --white: #ffffff;
    --line: rgba(255,255,255,0.75);
    --paper: #ffffff;
    --shirt: #c3d3ea;
    --shirt-light: #e8eef7;
    --denim: #3a5783;
    --backdrop: #e4e1dc;
    --hair: #d9bd8c;
    --wall: #3e5a66;
  }
  * { margin: 0; padding: 0; box-sizing: border-box; }
  html, body { width: 846px; height: 1200px; overflow: hidden; background: var(--paper); }
  .poster {
    position: relative;
    width: 846px;
    height: 1200px;
    background: var(--paper);
    font-family: "Raleway", sans-serif;
    color: var(--white);
  }
  .hero-photo {
    position: absolute;
    left: 36px; top: 36px;
    width: 773px; height: 561px;
    background:
      linear-gradient(180deg, rgba(217,189,140,0.85) 0%, rgba(217,189,140,0) 7%),
      linear-gradient(180deg, rgba(0,0,0,0) 62%, rgba(58,87,131,0.9) 72%, var(--denim) 92%, var(--wall) 100%),
      radial-gradient(ellipse 30% 28% at 50% 44%, var(--shirt-light) 0%, rgba(232,238,247,0) 100%),
      linear-gradient(90deg, var(--backdrop) 0%, var(--backdrop) 18%, var(--shirt) 32%, var(--shirt) 88%, #9fb4d0 100%);
  }
  .info-panel {
    position: absolute;
    left: 36px; top: 597px;
    width: 773px; height: 563px;
    background: var(--teal);
  }
  .frame-lines {
    position: absolute;
    left: 0; top: 0;
    width: 846px; height: 1200px;
    pointer-events: none;
  }
  .price-badge {
    position: absolute;
    left: 26px; top: 19px;
    width: 240px; height: 240px;
    border-radius: 50%;
    background: var(--wine);
    display: flex;
    flex-direction: column;
    align-items: center;
    justify-content: center;
    text-align: center;
    font-size: 35px;
    line-height: 1.35;
  }
  .price-badge strong { font-weight: 700; }
  .brand {
    position: absolute;
    left: 0; width: 846px;
    top: 706px;
    text-align: center;
  }
  .brand-name {
    display: inline-flex;
    align-items: center;
    gap: 10px;
    font-size: 26px;
    font-weight: 500;
    letter-spacing: 2px;
    text-transform: uppercase;
  }
  .brand-square {
    width: 12px; height: 12px;
    background: var(--white);
  }
  .brand-rule {
    width: 326px; height: 1px;
    margin: 6px auto 4px;
    background: var(--line);
  }
  .brand-tagline {
    font-size: 9px;
    letter-spacing: 3.6px;
    text-transform: uppercase;
    font-weight: 500;
  }
  .headline {
    position: absolute;
    left: 0; width: 846px;
    top: 809px;
    text-align: center;
    font-size: 40px;
    font-weight: 500;
    line-height: 50px;
  }
  .headline strong { font-weight: 700; }
  .body-copy {
    position: absolute;
    left: 0; width: 846px;
    top: 925px;
    text-align: center;
    font-size: 21px;
    line-height: 28.5px;
  }
  .divider {
    position: absolute;
    left: 285px; top: 1053px;
    width: 276px; height: 1px;
    background: var(--line);
  }
  .website {
    position: absolute;
    left: 0; width: 846px;
    top: 1100px;
    text-align: center;
    font-size: 22px;
    font-weight: 700;
  }
</style>
</head>
<body>
  <main class="poster">
    <div class="hero-photo" role="img" aria-label="Foto: Maklerin in blau gestreifter Bluse und Jeans hält ein kleines weißes Hausmodell auf einem Klemmbrett, dazu Stift und Schlüsselbund"></div>
    <div class="info-panel"></div>

    <svg class="frame-lines" viewBox="0 0 846 1200" aria-hidden="true">
      <polyline points="219,701 71,701 71,71 774,71 774,701 627,701" fill="none" stroke="rgba(255,255,255,0.8)" stroke-width="1"/>
    </svg>

    <div class="price-badge">
      <span>Nur</span>
      <strong>1,99 %</strong>
      <span>Provision</span>
    </div>

    <div class="brand">
      <div class="brand-name"><span class="brand-square"></span>Haldwick Immobilien</div>
      <div class="brand-rule"></div>
      <div class="brand-tagline">Immobilien &amp; Baufinanzierung</div>
    </div>

    <h1 class="headline">Wir spenden 5 % unserer<br>Provision für <strong>Ihren Verein!</strong></h1>

    <p class="body-copy">Sie kennen jemanden, der eine Immobilie verkaufen<br>möchte? Wir kümmern uns um den Verkauf und Sie<br>erhalten 5% unserer Provision!</p>

    <div class="divider"></div>

    <p class="website">www.immobilien-haldwick.de</p>
  </main>
</body>
</html>
```